Harborline Renewal Business Card Design

Professional and clean design. The design colors should flow with the logo. Two-sided card with the website on the back which is:

www.HarborlineRenewal.example.

"Specializing in Water Damage Restoration"

On the front I need the name, email, phone, and logo.

Name: Darnell Quisby
Email: Darnell@HarborlineRenewal.example
Phone: 555-318-2046 for now

I only have the Preview and Thumbnail right now but should have the source files uploaded within a day or two.

Target Market(s)

Flood victims, home owners with water damage from busted pipes etc...

Industry/Entity Type

Business

Contact Information for Business Card

Name: Darnell Quisby

Font styles to use
Serif
Sans Serif

Requirements
Must have
• Business Card Details Info

```html
<!DOCTYPE html>
<html lang="en">
<head>
<meta charset="utf-8">
<title>Harborline Renewal Business Card</title>
<link rel="stylesheet" href="https://fonts.googleapis.com/css2?family=Cinzel:wght@400;600;700&family=PT+Sans:wght@400&display=swap">
<style>
  :root {
    --page-bg: #e9edf0;
    --card-white: #f7f8f9;
    --brand-blue: #1fa3d3;
    --brand-blue-deep: #1489c0;
    --brand-blue-light: #4cc3e8;
    --wave-light: #8fdcf3;
    --text-white: #ffffff;
    --shadow: rgba(20, 60, 90, 0.22);
  }
  * { box-sizing: border-box; margin: 0; padding: 0; }
  html, body { width: 1200px; height: 780px; overflow: hidden; }
  body {
    background: var(--page-bg);
    position: relative;
    font-family: "PT Sans", sans-serif;
  }
  .card {
    position: absolute;
    top: 50px;
    width: 388px;
    height: 680px;
    border-radius: 22px;
    overflow: hidden;
    box-shadow: 0 12px 30px var(--shadow);
  }
  .card--front { left: 170px; background: var(--card-white); }
  .card--back {
    left: 642px;
    background: linear-gradient(165deg, var(--brand-blue-light) 0%, var(--brand-blue) 55%, var(--brand-blue-deep) 100%);
  }
  .card__waves { position: absolute; inset: 0; width: 100%; height: 100%; }

  .brand {
    position: absolute;
    left: 0; right: 0;
    text-align: center;
    font-family: "Cinzel", serif;
    font-weight: 700;
  }
  .brand__mark {
    display: block;
    width: 64px; height: 64px;
    margin: 0 auto 14px;
    border-radius: 50%;
  }
  .brand__name { display: block; font-size: 33px; letter-spacing: 1px; line-height: 1; }
  .brand__sub {
    display: block;
    font-size: 15px;
    letter-spacing: 9px;
    padding-left: 9px;
    margin-top: 8px;
    line-height: 1;
  }

  .card--front .brand { top: 64px; color: var(--brand-blue); }
  .card--front .brand__mark { background: var(--brand-blue); }
  .tagline {
    position: absolute;
    top: 222px; left: 0; right: 0;
    text-align: center;
    font-size: 15px;
    line-height: 1.2;
    color: var(--brand-blue);
  }

  .contact {
    position: absolute;
    left: 34px; right: 24px;
    top: 440px;
    color: var(--text-white);
  }
  .contact__name {
    font-family: "Cinzel", serif;
    font-weight: 700;
    font-size: 24px;
    letter-spacing: 1px;
    margin-bottom: 28px;
  }
  .contact__line { font-size: 16px; line-height: 1.45; }

  .card--back .brand { top: 222px; color: var(--text-white); }
  .card--back .brand__mark { background: var(--text-white); }
  .card--back .website {
    position: absolute;
    top: 382px; left: 0; right: 0;
    text-align: center;
    font-size: 16px;
    line-height: 1.2;
    color: var(--text-white);
  }
</style>
</head>
<body>

  <section class="card card--front" aria-label="Business card front">
    <svg class="card__waves" viewBox="0 0 388 680" preserveAspectRatio="none" aria-hidden="true">
      <defs>
        <linearGradient id="frontBlue" x1="0" y1="0" x2="0" y2="1">
          <stop offset="0" stop-color="#33b6e0"/>
          <stop offset="1" stop-color="#1a97cc"/>
        </linearGradient>
      </defs>
      <path d="M0 250 Q180 330 388 360 L388 680 L0 680 Z" fill="url(#frontBlue)"/>
      <path d="M0 250 Q180 330 388 360 L388 395 Q190 370 0 285 Z" fill="#8fdcf3" opacity="0.55"/>
    </svg>
    <div class="brand">
      <span class="brand__mark"></span>
      <span class="brand__name">HARBORLINE</span>
      <span class="brand__sub">RENEWAL</span>
    </div>
    <p class="tagline">Specializing in Water Damage Restoration</p>
    <div class="contact">
      <p class="contact__name">Darnell Quisby</p>
      <p class="contact__line">555-318-2046</p>
      <p class="contact__line">Darnell@HarborlineRenewal.example</p>
      <p class="contact__line">www.HarborlineRenewal.example</p>
    </div>
  </section>

  <section class="card card--back" aria-label="Business card back">
    <svg class="card__waves" viewBox="0 0 388 680" preserveAspectRatio="none" aria-hidden="true">
      <path d="M0 120 Q200 60 388 110 L388 150 Q200 100 0 160 Z" fill="#ffffff" opacity="0.07"/>
      <path d="M0 420 Q190 360 388 400 L388 680 L0 680 Z" fill="#ffffff" opacity="0.08"/>
    </svg>
    <div class="brand">
      <span class="brand__mark"></span>
      <span class="brand__name">HARBORLINE</span>
      <span class="brand__sub">RENEWAL</span>
    </div>
    <p class="website">www.HarborlineRenewal.example</p>
  </section>

</body>
</html>
```